Property management company looking for modern card design

We at Blue Heron Partners provides property management services for its residential and commercial properties, with expertise in all categories of multifamily, industrial and office projects throughout California.

We need a business card design that is professional and modern designed business card. In our field, clients get hundreds of business cards, we would like our card to stand out.

Please avoid small print.

Target Market(s)

Professionals and high end clients

Industry/Entity Type

Financial Planning

Contact Information for Business Card

Company Name: Blue Heron Partners, Name, email, license #, phone number, website blueheronpartners.com

Font styles to use
Sans Serif

Requirements
Must have
• The card design needs to be adaptable because there is a possibly we will be expanding into different sectors other than real estate. The card design should be focused on financial planning and asset management.
Nice to have
• Modern and simple business card. Eye catching. Non-standard size/shaped cards would be great.
• blueheronpartners.com
Should not have
• Too many bright color or any pictures or shapes of real estate stuff.

```html
<!DOCTYPE html>
<html lang="en">
<head>
<meta charset="utf-8">
<title>Blue Heron Partners – Business Card</title>
<link rel="stylesheet" href="https://fonts.googleapis.com/css2?family=Poppins:wght@500&family=Cabin:wght@400;600&family=Arimo:wght@700&display=swap">
<style>
  :root {
    --backdrop: #7a4520;
    --card: #eef0ec;
    --brand-red: #a30010;
    --mark-red: #b0101a;
    --ink: #23282b;
    --rule: #45424a;
    --web-grey: #4a4a4f;
  }
  * { margin: 0; padding: 0; box-sizing: border-box; }
  html, body { width: 900px; height: 1200px; overflow: hidden; }
  body { background: var(--backdrop); position: relative; }

  .card { position: absolute; background: var(--card); box-shadow: 0 2px 8px rgba(0,0,0,.25); }
  .card--front { left: 300px; top: 142px; width: 300px; height: 527px; }
  .card--back  { left: 185px; top: 741px; width: 528px; height: 301px; }

  .brand-dot { position: absolute; border-radius: 50%; background: var(--mark-red); }
  .card--front .brand-dot { left: 112px; top: 74px; width: 76px; height: 76px; }
  .card--back  .brand-dot { left: 231px; top: 87px; width: 76px; height: 76px; }

  .brand-name {
    position: absolute; left: 0; width: 100%; text-align: center;
    font-family: "Poppins", sans-serif; font-weight: 500; font-size: 26px;
    line-height: 1; letter-spacing: 4px; color: var(--brand-red);
  }
  .card--front .brand-name { top: 173px; }
  .card--back  .brand-name { top: 191px; }

  .rule { position: absolute; height: 3px; background: var(--rule); }

  .holder {
    position: absolute; right: 31px; text-align: right;
    font-family: "Cabin", sans-serif; color: var(--ink); line-height: 1;
  }
  .holder__name { top: 263px; font-size: 30px; font-weight: 600; }
  .holder__role { top: 299px; font-size: 13px; font-weight: 400; }

  .contact {
    position: absolute; right: 32px; text-align: right;
    font-family: "Cabin", sans-serif; font-weight: 600; font-size: 12px;
    line-height: 1; color: var(--ink); white-space: nowrap;
  }
  .contact--email   { top: 419px; }
  .contact--phone   { top: 442px; }
  .contact--license { top: 464px; }
  .contact--web     { top: 487px; font-size: 17px; }

  .back-web {
    position: absolute; left: 0; width: 100%; top: 266px; text-align: center;
    font-family: "Arimo", sans-serif; font-weight: 700; font-size: 17px;
    line-height: 1; color: var(--web-grey);
  }
</style>
</head>
<body>
  <section class="card card--front" aria-label="Business card front">
    <div class="brand-dot"></div>
    <div class="brand-name">Blue Heron</div>
    <div class="rule" style="left:41px; width:259px; top:222px;"></div>
    <div class="rule" style="left:0; width:215px; top:230px;"></div>

    <div class="holder holder__name">Daniel Reyes</div>
    <div class="holder holder__role">managing director</div>

    <div class="rule" style="left:40px; width:260px; top:383px;"></div>
    <div class="rule" style="left:0; width:215px; top:390px;"></div>

    <div class="contact contact--email">daniel.reyes@blueheronpartners.com</div>
    <div class="contact contact--phone">415-208-7391</div>
    <div class="contact contact--license">License Nr:482913</div>
    <div class="contact contact--web">blueheronpartners.com</div>
  </section>

  <section class="card card--back" aria-label="Business card back">
    <div class="brand-dot"></div>
    <div class="brand-name">Blue Heron</div>
    <div class="rule" style="left:81px; width:447px; top:244px;"></div>
    <div class="rule" style="left:0; width:433px; top:251px;"></div>
    <div class="back-web">blueheronpartners.com</div>
  </section>
</body>
</html>
```